Resposive web site in 4 languages + image gallery + logo design

We need a web page, which will work on all devices.
I have uploaded web page concept.
Company name: Praxelun
Industry/Entity Type
It Company
Logo Text
quality matters
Coding
Coded - Design and coding required
Number of Pages Required
1 page

```html
<!DOCTYPE html>
<html lang="en">
<head>
<meta charset="utf-8">
<title>Praxelun — Woodworks, Stoneworks, Restoration</title>
<link href="https://fonts.googleapis.com/css2?family=Roboto:wght@400;500;700&family=Open+Sans:wght@400;600&display=swap" rel="stylesheet">
<style>
:root{
  --blue:#1a6fbd;
  --blue-deep:#1565b0;
  --blue-band:rgba(21,101,176,.92);
  --ink:#444;
  --ink-soft:#666;
  --grey-bg:#f1f1f1;
  --rule:#d6d6d6;
  --dark:#262626;
  --dark-field:#1c1c1c;
  --field-line:#444;
  --gold:#f7b500;
  --gold-deep:#e79c00;
  --white:#fff;
}
*{box-sizing:border-box;margin:0;padding:0}
html,body{width:1200px;height:2528px;overflow:hidden}
body{position:relative;background:var(--white);font-family:"Open Sans",Arial,sans-serif;color:var(--ink)}

/* header */
.site-header{position:absolute;left:0;top:0;width:1200px;height:113px;border-top:3px solid var(--blue-deep);background:var(--white)}
.brand{position:absolute;left:131px;top:36px;font-family:"Roboto",Arial,sans-serif;font-weight:700;font-size:31px;color:var(--blue);letter-spacing:-.3px}
.main-nav{position:absolute;left:400px;top:49px;display:flex}
.main-nav a{font-family:"Roboto",Arial,sans-serif;font-size:12px;color:#222;text-decoration:none;letter-spacing:.3px}
.main-nav a.active{color:var(--blue)}
.main-nav a:nth-child(1){margin-right:45px}
.main-nav a:nth-child(2){margin-right:43px}
.lang-select{position:absolute;left:947px;top:42px;width:74px;height:27px;border:1px solid #c9c9c9;border-radius:3px;display:flex;align-items:center;padding-left:9px;gap:6px;font-family:"Roboto",Arial,sans-serif;font-size:11px;color:var(--blue)}
.lang-select .flag{width:12px;height:8px;background:#b9c6dc}
.social-dot{position:absolute;left:1037px;top:41px;width:28px;height:28px;border-radius:50%;background:#3b5998}

/* hero */
.hero{position:absolute;left:0;top:113px;width:1200px;height:460px;background:linear-gradient(120deg,#c98b45 0%,#e2b072 30%,#8db6de 55%,#3f87c9 100%)}
.hero-band{position:absolute;left:0;bottom:0;width:100%;height:84px;background:var(--blue-band)}
.hero-title{position:absolute;left:133px;top:498px;font-family:"Roboto",Arial,sans-serif;font-weight:700;font-size:28px;line-height:34px;color:var(--white)}
.hero-sub{position:absolute;left:135px;top:536px;font-size:14px;line-height:20px;color:var(--white)}
.btn-quote{position:absolute;left:381px;top:506px;width:155px;height:42px;border-radius:3px;background:linear-gradient(var(--gold),var(--gold-deep));font-family:"Roboto",Arial,sans-serif;font-weight:700;font-size:14px;color:#5a3a00;display:flex;align-items:center;justify-content:center;letter-spacing:.3px}
.hero-dots{position:absolute;left:1006px;top:528px}

/* services */
.section{position:absolute;left:0;width:1200px}
.section-grey{background:var(--grey-bg);border-top:1px solid var(--rule);border-bottom:1px solid var(--rule)}
.section-title{position:absolute;left:0;width:100%;text-align:center;font-family:"Roboto",Arial,sans-serif;font-weight:700;font-size:30px;color:var(--blue)}
.card{position:absolute;width:302px;height:235px;background:var(--white);box-shadow:0 0 6px rgba(0,0,0,.25);padding:4px}
.card .photo{width:294px;height:170px}
.card .caption{height:57px;background:var(--blue);display:flex;align-items:center;justify-content:space-between;padding:0 20px;color:var(--white);font-family:"Roboto",Arial,sans-serif;font-size:24px}
.arrow-btn{width:22px;height:22px;border-radius:50%;background:#0f4f8c;display:flex;align-items:center;justify-content:center}
.service-text{position:absolute;width:600px}
.service-text h3{font-family:"Roboto",Arial,sans-serif;font-weight:500;font-size:19px;color:var(--blue);margin-bottom:18px;letter-spacing:.3px}
.service-text p{font-size:11.6px;line-height:19px;color:var(--ink);margin-bottom:18px}
.tags{display:flex;gap:22px;list-style:none;font-size:10.5px;color:var(--blue);margin-top:6px}
.tags li::before{content:"»";margin-right:6px;font-weight:700}

/* about */
.about-text{position:absolute;left:131px;top:1783px;width:600px;font-size:11.6px;line-height:19px}
.about-text p{margin-bottom:18px}
.sign{position:absolute;left:135px;top:1923px;font-size:14px;line-height:25px;color:var(--ink)}
.sign span{color:var(--blue)}
.framed{position:absolute;background:var(--white);box-shadow:0 0 6px rgba(0,0,0,.25);padding:4px}

/* footer */
.site-footer{position:absolute;left:0;top:2071px;width:1200px;height:457px;background:var(--dark);color:#ccc}
.footer-h{position:absolute;font-family:"Roboto",Arial,sans-serif;font-weight:500;font-size:14px;color:var(--white)}
.contact-list{position:absolute;left:133px;top:94px;font-size:11.5px;line-height:17px;list-style:none}
.contact-list li{display:flex;gap:10px;margin-bottom:18px}
.contact-list li.tight{margin-bottom:0}
.socials{position:absolute;left:133px;top:249px;display:flex;gap:6px}
.socials span{width:34px;height:34px;border:2px solid #ddd;border-radius:50%}
.copyright{position:absolute;left:133px;top:344px;font-size:11.5px}
.quote-form label{position:absolute;left:564px;font-size:11px;color:#ccc;letter-spacing:.3px}
.quote-form .field{position:absolute;left:657px;width:303px;height:40px;background:var(--dark-field);border:1px solid var(--field-line);border-radius:2px}
.btn-send{position:absolute;left:873px;top:377px;width:87px;height:32px;border-radius:3px;background:var(--blue);color:var(--white);font-size:12px;display:flex;align-items:center;justify-content:center}
</style>
</head>
<body>

<header class="site-header">
  <div class="brand">Praxelun</div>
  <nav class="main-nav">
    <a class="active" href="#services">SERVICES</a>
    <a href="#about">ABOUT US</a>
    <a href="#contact">CONTACT</a>
  </nav>
  <div class="lang-select"><span class="flag"></span>ENG
    <svg width="8" height="6" viewBox="0 0 8 6"><path d="M1 1l3 3 3-3" stroke="#1a6fbd" fill="none" stroke-width="1.3"/></svg>
  </div>
  <span class="social-dot"></span>
</header>

<section class="hero">
  <div role="img" aria-label="Carpenter in a hard hat building a timber roof frame against a blue sky" style="position:absolute;inset:0"></div>
  <div class="hero-band"></div>
</section>
<div class="hero-title">WOODWORKS</div>
<div class="hero-sub">Are you interested in an estimate?</div>
<div class="btn-quote">GET A QUOTE</div>
<svg class="hero-dots" width="70" height="16" viewBox="0 0 70 16">
  <circle cx="7" cy="8" r="6" fill="#fff"/>
  <circle cx="32" cy="8" r="5.5" fill="none" stroke="#fff" stroke-width="2"/>
  <circle cx="56" cy="8" r="5.5" fill="none" stroke="#fff" stroke-width="2"/>
</svg>

<section class="section" id="services" style="top:573px;height:416px">
  <h2 class="section-title" style="top:42px">OUR SERVICES</h2>
</section>
<div class="card" style="left:131px;top:704px">
  <div class="photo" role="img" aria-label="Wooden dining table with chairs" style="background:linear-gradient(135deg,#e8d8c4,#8a4a22 60%,#5a2e14)"></div>
  <div class="caption">
    <span class="arrow-btn"><svg width="8" height="10"><path d="M6 1L2 5l4 4" stroke="#fff" fill="none" stroke-width="1.6"/></svg></span>
    Furniture
    <span class="arrow-btn"><svg width="8" height="10"><path d="M2 1l4 4-4 4" stroke="#fff" fill="none" stroke-width="1.6"/></svg></span>
  </div>
</div>
<div class="service-text" style="left:468px;top:702px">
  <h3>WOODWORKS</h3>
  <p>Timber is, in essence, a natural and warm material. Wood is also relatively durable and easy to work with, which has made it a favourite of builders throughout history.</p>
  <p>Our goal is to offer suitable products and quality furniture with installation and after-sales service to all of our clients. In order to achieve this, we're ready to help our clients in all stages of construction from design to production and maintenance.</p>
  <ul class="tags"><li>Furniture</li><li>Windows</li><li>Doors</li><li>Staircases</li><li>Woodcarving</li><li>Graining</li></ul>
</div>

<section class="section section-grey" style="top:989px;height:352px"></section>
<div class="service-text" style="left:131px;top:1046px;width:603px">
  <h3>STONEWORKS</h3>
  <p>The natural stone found in the ground has been used in construction for centuries because of its durability. A structure built by a skilled craftsman from natural stone is unique, genuine and durable, and perfect for our bracing climate.</p>
  <p style="margin-top:32px">Our experienced craftsmen are ready to help you in all stages of construction from planning to completion.</p>
  <ul class="tags"><li>Walls</li><li>Terraces</li><li>Paths</li><li>Outdoor kitchens</li><li>Fireplaces</li><li>Smokeries</li><li>Fences</li></ul>
</div>
<div class="card" style="left:768px;top:1048px">
  <div class="photo" role="img" aria-label="Stacked natural stone wall" style="background:linear-gradient(160deg,#d9a270,#b46a3c 50%,#e0b98e)"></div>
  <div class="caption">
    <span class="arrow-btn"><svg width="8" height="10"><path d="M6 1L2 5l4 4" stroke="#fff" fill="none" stroke-width="1.6"/></svg></span>
    Walls
    <span class="arrow-btn"><svg width="8" height="10"><path d="M2 1l4 4-4 4" stroke="#fff" fill="none" stroke-width="1.6"/></svg></span>
  </div>
</div>

<div class="card" style="left:131px;top:1385px">
  <div class="photo" role="img" aria-label="Craftsman varnishing a wooden chair back" style="background:linear-gradient(135deg,#c98d5c,#6b3a1c 55%,#3a2012)"></div>
  <div class="caption">
    <span class="arrow-btn"><svg width="8" height="10"><path d="M6 1L2 5l4 4" stroke="#fff" fill="none" stroke-width="1.6"/></svg></span>
    Furniture
    <span class="arrow-btn"><svg width="8" height="10"><path d="M2 1l4 4-4 4" stroke="#fff" fill="none" stroke-width="1.6"/></svg></span>
  </div>
</div>
<div class="service-text" style="left:467px;top:1382px">
  <h3>RESTORATION</h3>
  <p style="padding-left:8px">It's good to see that fixing old things has become popular again in recent years and people are trying to find ways to preserve valuable old windows and pieces of furniture before deciding to replace them.</p>
  <p style="padding-left:8px">It is possible to give a new life to almost any wooden door, window, piece of furniture or staircase. The extensive experience of our craftsmen will help you achieve the desired result.</p>
  <ul class="tags" style="padding-left:8px"><li>Furniture</li><li>Windows</li><li>Doors</li><li>Staircases</li><li>Floors</li><li>Special Projects</li></ul>
</div>

<section class="section section-grey" id="about" style="top:1677px;height:394px;border-bottom:none">
  <h2 class="section-title" style="top:40px">ABOUT US</h2>
</section>
<div class="about-text">
  <p>Praxelun is a company whose business operations include making wooden products, restoration and building structures from natural stone. All of our products are made by craftsmen and specialists who have extensive experience and knowledge in their fields.</p>
  <p>The products we offer are always handmade and we take the requests and ideas of the specific client into account. We always strive to achieve the best possible quality.</p>
</div>
<div class="sign">Quality matters,<br><span>Praxelun</span></div>
<div class="framed" style="left:763px;top:1783px;width:300px;height:234px">
  <div role="img" aria-label="Senior craftsman at his workbench in a workshop" style="width:100%;height:100%;background:linear-gradient(135deg,#5a4632,#a88a66 50%,#3d3026)"></div>
</div>

<footer class="site-footer" id="contact">
  <div class="footer-h" style="left:133px;top:50px">CONTACT</div>
  <ul class="contact-list">
    <li><svg width="9" height="12" viewBox="0 0 9 12"><path d="M4.5 0A4.5 4.5 0 0 0 0 4.5C0 8 4.5 12 4.5 12S9 8 9 4.5A4.5 4.5 0 0 0 4.5 0zm0 6.2a1.7 1.7 0 1 1 0-3.4 1.7 1.7 0 0 1 0 3.4z" fill="#ccc"/></svg>
      <span>Kaselaane 7<br>10115 Tallinn<br>ESTONIA</span></li>
    <li class="tight"><svg width="11" height="11" viewBox="0 0 11 11"><path d="M2 0l2 2.5-1 1.3a6 6 0 0 0 4.2 4.2l1.3-1L11 9l-1.5 2C4 11 0 7 0 1.5z" fill="#ccc"/></svg>
      <span>Telephone: +372 55 01 2233</span></li>
    <li><svg width="12" height="10" viewBox="0 0 12 10"><rect x=".6" y=".6" width="10.8" height="8.8" fill="none" stroke="#ccc" stroke-width="1.2"/><path d="M.6 .8L6 5.4 11.4.8" fill="none" stroke="#ccc" stroke-width="1.2"/></svg>
      <span>e-mail: info@praxelun.ee</span></li>
  </ul>
  <div class="socials"><span></span><span></span><span></span><span></span></div>
  <div class="copyright">Copyright © 2016 Praxelun All rightreserved</div>

  <div class="footer-h" style="left:564px;top:50px">PLEASE FILL IN THE FOLLOWING FIELDS IF YOU WOULD LIKE A PRICE QUOTE</div>
  <div class="quote-form">
    <label style="top:105px">NAME</label><div class="field" style="top:91px"></div>
    <label style="top:152px">TELEPHONE</label><div class="field" style="top:138px"></div>
    <label style="top:200px">E-MAIL</label><div class="field" style="top:187px"></div>
    <label style="top:248px">MESSAGE</label><div class="field" style="top:234px;height:128px"></div>
    <div class="btn-send">Send</div>
  </div>
</footer>

</body>
</html>
```